Business Card Design

I need business cards designed for a new company i have started that makes cakes, particularly themed kids cakes with a really modern design and I would like to have my business cards reflect this. I have attached some photos of cakes I have made and would like some to be used.

Industry/Entity Type

Business

Contact Information for Business Card

Business Name: Tarts and Treats by Maren
Mobile: 0492 815 063
email: maren@tartsandtreatsbymaren.example.au
Instagram: instagram.com/tartsandtreatsbymaren/
Facebook: fb.me/tartsandtreatsbymaren

Colors
e667a6
b768aa
3276b5

Requirements
Must have
• Business Name: Tarts and Treats by Maren
• Mobile: 0492 815 063
• email: maren@tartsandtreatsbymaren.example.au
• Instagram: instagram.com/tartsandtreatsbymaren/
• Facebook: fb.me/tartsandtreatsbymaren
Nice to have
• 2 to 3 pictures of my cakes

```html
<!DOCTYPE html>
<html lang="en">
<head>
<meta charset="utf-8">
<title>Tarts and Treats by Maren – Business Card</title>
<link rel="stylesheet" href="https://fonts.googleapis.com/css2?family=Open+Sans:wght@400;600;700&display=swap">
<style>
  :root {
    --backdrop: #ece8ea;
    --purple: #b56bb0;
    --purple-deep: #9a4f97;
    --pink: #e667a6;
    --pink-light: #f08cbd;
    --white: #ffffff;
    --card-white: #f7f6f7;
    --shadow: rgba(60, 30, 55, 0.18);
  }
  * { margin: 0; padding: 0; box-sizing: border-box; }
  html, body {
    width: 1200px;
    height: 843px;
    overflow: hidden;
    background: var(--backdrop);
    font-family: "Open Sans", Arial, sans-serif;
  }
  .canvas { position: relative; width: 1200px; height: 843px; }
  .card {
    position: absolute;
    width: 560px;
    height: 320px;
    overflow: hidden;
    box-shadow: 0 10px 26px var(--shadow);
  }

  /* Back of card */
  .card--back {
    left: 60px;
    top: 80px;
    background: linear-gradient(100deg, var(--purple) 0%, #c17dbd 45%, var(--purple) 60%, var(--purple-deep) 100%);
    display: flex;
    align-items: center;
    justify-content: center;
  }
  .wordmark {
    display: flex;
    align-items: center;
    gap: 14px;
    font-weight: 600;
    letter-spacing: 0.5px;
  }
  .wordmark__dot { width: 14px; height: 14px; border-radius: 50%; flex: none; }
  .card--back .wordmark { color: var(--white); font-size: 30px; }
  .card--back .wordmark__dot { background: var(--white); }

  /* Front of card */
  .card--front {
    left: 580px;
    top: 440px;
    background: linear-gradient(100deg, var(--pink) 0%, var(--pink-light) 40%, var(--pink) 60%, var(--pink) 100%);
  }
  .front-curve { position: absolute; inset: 0; }
  .contact-list {
    position: absolute;
    left: 30px;
    top: 26px;
    list-style: none;
    color: var(--white);
    font-size: 12px;
    line-height: 19px;
  }
  .contact-list li { display: flex; align-items: center; gap: 9px; }
  .contact-icon { width: 12px; height: 12px; flex: none; }
  .contact-icon--plain { background: var(--white); border-radius: 2px; }
  .person {
    position: absolute;
    left: 30px;
    top: 190px;
    color: var(--white);
  }
  .person__name { font-size: 17px; font-weight: 700; letter-spacing: 0.5px; }
  .person__role { font-size: 13px; margin-top: 2px; }
  .card--front .wordmark {
    position: absolute;
    left: 290px;
    top: 178px;
    color: var(--purple);
    font-size: 24px;
    line-height: 1.2;
    gap: 12px;
  }
  .card--front .wordmark__dot { background: var(--pink); width: 12px; height: 12px; }
</style>
</head>
<body>
<main class="canvas">

  <section class="card card--back" aria-label="Card back">
    <div class="wordmark">
      <span class="wordmark__dot"></span>
      <span class="wordmark__name">Tarts and Treats by Maren</span>
    </div>
  </section>

  <section class="card card--front" aria-label="Card front">
    <svg class="front-curve" width="560" height="320" viewBox="0 0 560 320" aria-hidden="true">
      <path d="M560 70 C380 72 180 140 165 320 L560 320 Z" fill="var(--purple)"/>
      <path d="M560 84 C392 88 196 150 182 320 L560 320 Z" fill="var(--card-white)"/>
    </svg>

    <ul class="contact-list">
      <li>
        <svg class="contact-icon" viewBox="0 0 12 12" aria-hidden="true"><rect x="3" y="0.5" width="6" height="11" rx="1.2" fill="none" stroke="#fff" stroke-width="1.2"/><circle cx="6" cy="9.6" r="0.8" fill="#fff"/></svg>
        <span>0492 815 063</span>
      </li>
      <li>
        <svg class="contact-icon" viewBox="0 0 12 12" aria-hidden="true"><rect x="0.6" y="2.5" width="10.8" height="7.5" rx="1" fill="none" stroke="#fff" stroke-width="1.2"/><path d="M1 3 L6 7 L11 3" fill="none" stroke="#fff" stroke-width="1.2"/></svg>
        <span>maren@tartsandtreatsbymaren.example.au</span>
      </li>
      <li>
        <span class="contact-icon contact-icon--plain"></span>
        <span>tartsandtreatsbymaren</span>
      </li>
      <li>
        <span class="contact-icon contact-icon--plain"></span>
        <span>tartsandtreatsbymaren</span>
      </li>
    </ul>

    <div class="person">
      <p class="person__name">JONAH PELL</p>
      <p class="person__role">CEO/Founder</p>
    </div>

    <div class="wordmark">
      <span class="wordmark__dot"></span>
      <span class="wordmark__name">Tarts and Treats<br>by Maren</span>
    </div>
  </section>

</main>
</body>
</html>
```